Wholesale in Gold Jewellery & Gold Bullion

We are an established gold jewellery and gold bullion wholesaler selling these products to international clients. We already have a name and logo of our company, hence please view attached current card design. We need a completely new design to compliment our business and industry and the final design should be new and elegant.

Contact Information for Business Card

New card details must be same as per current card. Like logo, name, tel no. & etc.

Colors

Designer to choose colors to be used in the design.

```html
<!DOCTYPE html>
<html lang="en">
<head>
<meta charset="utf-8">
<title>Harlow &amp; Co Business Card</title>
<link href="https://fonts.googleapis.com/css2?family=Libre+Baskerville:wght@700&family=Montserrat:wght@400;500;600&display=swap" rel="stylesheet">
<style>
  :root {
    --stage: #8c8c8c;
    --card: #efefef;
    --gold: #c98a20;
    --espresso: #241816;
    --ink: #3a3a3a;
    --white: #ffffff;
  }
  html, body {
    margin: 0;
    width: 1200px;
    height: 861px;
    overflow: hidden;
    background: var(--stage);
  }
  .card {
    position: absolute;
    left: 150px;
    top: 174px;
    width: 900px;
    height: 514px;
    background: var(--card);
    box-shadow: 0 10px 30px rgba(0,0,0,0.25);
    overflow: hidden;
    font-family: "Montserrat", sans-serif;
  }
  .brand {
    position: absolute;
    left: 120px;
    top: 62px;
    display: flex;
    align-items: center;
    gap: 26px;
  }
  .brand-dot {
    width: 96px;
    height: 96px;
    border-radius: 50%;
    background: var(--gold);
  }
  .brand-name {
    font-family: "Libre Baskerville", serif;
    font-weight: 700;
    font-size: 26px;
    color: #1c1c1c;
    letter-spacing: 0.5px;
    margin-top: -40px;
  }
  .band {
    position: absolute;
    left: 0;
    top: 196px;
    width: 100%;
    height: 70px;
    display: flex;
  }
  .band-gold { flex: 0 0 590px; background: var(--gold); }
  .band-dark { flex: 1; background: var(--espresso); }
  .band-dot {
    position: absolute;
    left: 552px;
    top: 192px;
    width: 78px;
    height: 78px;
    border-radius: 50%;
    background: var(--white);
  }
  .person {
    position: absolute;
    left: 215px;
    top: 204px;
    color: var(--white);
  }
  .person-name {
    font-weight: 600;
    font-size: 30px;
    line-height: 1.1;
  }
  .person-role {
    font-weight: 400;
    font-size: 24px;
    line-height: 1.1;
    opacity: 0.9;
  }
  .contacts {
    position: absolute;
    left: 262px;
    top: 300px;
    margin: 0;
    padding: 0;
    list-style: none;
    color: var(--ink);
    font-size: 21px;
  }
  .contacts li {
    display: flex;
    align-items: center;
    gap: 22px;
    height: 38px;
  }
  .contacts svg { width: 22px; height: 22px; flex: none; }
  .address {
    position: absolute;
    right: 70px;
    top: 300px;
    text-align: right;
    color: var(--ink);
    font-size: 17px;
    line-height: 1.35;
  }
</style>
</head>
<body>
  <div class="card">
    <div class="brand">
      <div class="brand-dot"></div>
      <div class="brand-name">HARLOW &amp; CO PTE LTD</div>
    </div>

    <div class="band"><div class="band-gold"></div><div class="band-dark"></div></div>
    <div class="band-dot"></div>

    <div class="person">
      <div class="person-name">Arjun Velamuri</div>
      <div class="person-role">Director</div>
    </div>

    <ul class="contacts">
      <li>
        <svg viewBox="0 0 24 24" aria-hidden="true"><rect x="7" y="2" width="10" height="20" rx="2" fill="none" stroke="#c98a20" stroke-width="2"/><line x1="10" y1="18" x2="14" y2="18" stroke="#c98a20" stroke-width="2"/></svg>
        +65 9123 4501
      </li>
      <li>
        <svg viewBox="0 0 24 24" aria-hidden="true"><path d="M6 3l3 0 2 5-2 2c1 2 3 4 5 5l2-2 5 2v3c0 1-1 2-2 2C10 20 4 14 4 5c0-1 1-2 2-2z" fill="#c98a20"/></svg>
        +65 6800 2200
      </li>
      <li>
        <svg viewBox="0 0 24 24" aria-hidden="true"><rect x="3" y="9" width="18" height="12" rx="1" fill="#c98a20"/><rect x="7" y="3" width="10" height="7" fill="none" stroke="#c98a20" stroke-width="2"/><rect x="6" y="13" width="8" height="2" fill="#efefef"/></svg>
        +65 6555 0148
      </li>
      <li>
        <svg viewBox="0 0 24 24" aria-hidden="true"><rect x="2" y="5" width="20" height="14" fill="#c98a20"/><path d="M2 5l10 8 10-8" fill="none" stroke="#efefef" stroke-width="2"/></svg>
        arjun@harlowco.com
      </li>
    </ul>

    <div class="address">12 Mercer Lane,<br>Singapore 208811</div>
  </div>
</body>
</html>
```